1876 Basins & Spouts Business Card

I'm wanting to get a business card designed. Our business is 1876 Basins & Spouts
Details for the card:

1876 Basins & Spouts
Name: Harold Vesk
Email: harold@1876basinsandspouts.com.au
Website: www.1876basinsandspouts.com.au
Mobile: 0438 260 947
Phone: 02 7481 3926

Font of Basins & Spouts is called Snell Roundhand. Not sue what font logo text is.

I'm thinking two sided but it doesn't have to be.

```html
<!DOCTYPE html>
<html lang="en">
<head>
<meta charset="utf-8">
<title>1876 Basins &amp; Spouts Business Card</title>
<link rel="stylesheet" href="https://fonts.googleapis.com/css2?family=Open+Sans:wght@400;700&display=swap">
<style>
  :root {
    --stage: #2a2a2a;
    --ink: #111111;
    --paper: #ffffff;
    --rule: #555555;
    --muted: #333333;
  }
  * { box-sizing: border-box; margin: 0; padding: 0; }
  html, body { width: 1200px; height: 900px; overflow: hidden; }
  body {
    background: var(--stage);
    font-family: "Open Sans", Arial, sans-serif;
    position: relative;
  }
  .card {
    position: absolute;
    left: 280px;
    width: 640px;
    height: 366px;
    overflow: hidden;
  }
  .card-front { top: 70px; background: var(--paper); color: var(--ink); }
  .card-back { top: 466px; background: var(--ink); color: var(--paper); }

  /* Front */
  .front-brand {
    position: absolute;
    left: 30px; top: 170px;
    width: 265px;
    text-align: center;
  }
  .brand-name {
    display: flex; align-items: center; justify-content: center; gap: 8px;
    font-size: 22px; font-weight: 400; line-height: 1.2; white-space: nowrap;
  }
  .brand-dot {
    width: 10px; height: 10px; border-radius: 50%; background: currentColor; flex: none;
  }
  .tagline { font-size: 10px; margin-top: 10px; letter-spacing: 0.2px; white-space: nowrap; }
  .divider {
    position: absolute; left: 305px; top: 120px;
    width: 2px; height: 160px; background: var(--rule);
  }
  .name-band {
    position: absolute; left: 330px; right: 0; top: 100px; height: 42px;
    background: var(--ink); color: var(--paper);
    display: flex; align-items: center; gap: 10px; padding-left: 14px;
  }
  .name-band svg { flex: none; }
  .person-name { font-size: 14px; line-height: 1.05; letter-spacing: 0.3px; }
  .person-name b { font-weight: 700; }
  .person-role { font-size: 10px; letter-spacing: 0.3px; }
  .contact-list {
    position: absolute; left: 340px; top: 156px;
    list-style: none; font-size: 13px; color: var(--muted);
  }
  .contact-list li { display: flex; align-items: center; gap: 10px; margin-bottom: 8px; line-height: 1.15; white-space: nowrap; }
  .contact-list svg { flex: none; }

  /* Back */
  .back-frame {
    position: absolute; inset: 28px 30px;
    border: 1.5px solid var(--paper);
  }
  .back-brand {
    position: absolute; left: 80px; top: 130px;
    display: flex; flex-direction: column; align-items: flex-start;
  }
  .back-brand .brand-name { font-size: 30px; }
  .back-brand .tagline { font-size: 11px; margin-left: 18px; margin-top: 8px; }
  .back-web {
    position: absolute; left: 0; right: 0; top: 262px;
    text-align: center; font-size: 11px; letter-spacing: 0.3px;
  }
</style>
</head>
<body>
  <section class="card card-front" aria-label="Card front">
    <div class="front-brand">
      <div class="brand-name"><span class="brand-dot"></span>1876 Basins &amp; Spouts</div>
      <p class="tagline">Pairing classic elegance with everyday function</p>
    </div>
    <div class="divider"></div>
    <div class="name-band">
      <svg width="22" height="22" viewBox="0 0 22 22" aria-hidden="true">
        <circle cx="11" cy="11" r="11" fill="#fff"/>
        <circle cx="11" cy="8.5" r="3.5" fill="#111"/>
        <path d="M4.5 18 Q11 10 17.5 18Z" fill="#111"/>
      </svg>
      <div>
        <p class="person-name"><b>HAROLD</b> VESK</p>
        <p class="person-role">DESIGNATION</p>
      </div>
    </div>
    <ul class="contact-list">
      <li>
        <svg width="18" height="18" viewBox="0 0 18 18" aria-hidden="true">
          <circle cx="9" cy="9" r="8" fill="none" stroke="#111" stroke-width="1.5"/>
          <path d="M6 5 L7.5 5 L8 7 L7 8 Q8 10 10 11 L11 10 L13 10.5 L13 12 Q9 13 6 9 Q5 7 6 5Z" fill="#111"/>
        </svg>
        <span>02 7481 3926<br>0438 260 947</span>
      </li>
      <li>
        <svg width="18" height="18" viewBox="0 0 18 18" aria-hidden="true">
          <g fill="none" stroke="#111" stroke-width="1.4">
            <circle cx="9" cy="9" r="8"/>
            <ellipse cx="9" cy="9" rx="3.5" ry="8"/>
            <path d="M1 9H17M2.5 5H15.5M2.5 13H15.5"/>
          </g>
        </svg>
        <span>www.1876basinsandspouts.com.au</span>
      </li>
      <li>
        <svg width="18" height="16" viewBox="0 0 18 16" aria-hidden="true">
          <rect x="0" y="1" width="18" height="14" fill="#111"/>
          <path d="M2 3 L9 9 L16 3" fill="none" stroke="#fff" stroke-width="1.5"/>
        </svg>
        <span>harold@1876basinsandspouts.com.au</span>
      </li>
    </ul>
  </section>

  <section class="card card-back" aria-label="Card back">
    <div class="back-frame"></div>
    <div class="back-brand">
      <div class="brand-name"><span class="brand-dot"></span>1876 Basins &amp; Spouts</div>
      <p class="tagline">Pairing classic elegance with everyday function</p>
    </div>
    <p class="back-web">www.1876basinsandspouts.com.au</p>
  </section>
</body>
</html>
```